Business card

We need a business card design for our company based in Auckland , New Zealand called 'Ridge + Studio Ltd'. We provide architectural services. We would like to see designs that use the max. three colours (such as white, black, grey) The final design should communicate financial safety and growth."
Also I will provide our company logo. I would like to the logo to be embeded onto our business card.

Target Market(s)

new residential house, alteration & addition & light commericila design & drafting service

Industry/Entity Type

Architecture

Contact Information for Business Card

Company name: ridge + studio Ltd.
Name: Mark Delford
Job title: architectural designer & Design LBP
email address: mark@rplusd.co.nz
mobile number: 02 5163 2290
web site: www.rplusd.co.nz

Requirements
Must have
• My project must have..
• - embeded logo (attached company logo)
• I don't have a bigger version for our company logo, but I have one old one, so you can remove the word from it)
• - insert the attached small BKTW logo & LBP logo
• - creative, simple and clear business card.
• - Max. three colours
Nice to have
• - Here are the samples I would like to share with you: http://www.plimvora.com/blog/minimalistic-business-card-designs/
• I would like to have my business card like one of the creation.
Should not have
• TBA

```html
<!DOCTYPE html>
<html lang="en">
<head>
<meta charset="utf-8">
<title>Ridge + Studio Ltd — Business Card</title>
<link rel="stylesheet" href="https://fonts.googleapis.com/css2?family=Arimo:wght@400&display=swap">
<style>
  :root {
    --canvas: #dcd8d3;
    --card-top: #f4f5f6;
    --card-bottom: #e3e5e7;
    --ink: #141414;
    --band-dark: #4a4a4a;
    --band-mid: #8a8886;
    --band-line: #d8d8d8;
    --footer: #0e0e0e;
    --footer-text: #bfaea4;
    --title-text: #ececec;
    --badge: #1c1c1c;
  }
  * { box-sizing: border-box; margin: 0; padding: 0; }
  html, body {
    width: 1200px; height: 969px; overflow: hidden;
    background: var(--canvas);
    font-family: "Arimo", Arial, sans-serif;
  }
  .card {
    position: absolute; left: 100px; top: 200px;
    width: 1000px; height: 568px;
    border-radius: 6px; overflow: hidden;
    background: linear-gradient(180deg, var(--card-top), var(--card-bottom));
    box-shadow: 0 10px 30px rgba(0,0,0,0.18);
  }
  .brand {
    position: absolute; left: 109px; top: 92px;
    display: flex; align-items: center; gap: 22px;
  }
  .brand-circle {
    width: 140px; height: 140px; border-radius: 50%;
    border: 10px solid var(--ink);
  }
  .brand-name {
    font-size: 28px; font-weight: 400; color: var(--ink);
    white-space: nowrap;
  }
  .partner {
    position: absolute; left: 560px; top: 108px; height: 96px;
    display: flex; align-items: center;
  }
  .partner-name {
    font-size: 30px; font-weight: 400; color: var(--ink);
    padding-right: 26px;
    border-right: 2px solid rgba(20,20,20,0.6);
    height: 96px; display: flex; align-items: center;
  }
  .badge {
    position: absolute; left: 760px; top: 95px;
    width: 138px; height: 138px; border-radius: 50%;
    background: var(--badge);
  }
  .name-band {
    position: absolute; left: 0; top: 337px; width: 100%; height: 82px;
    display: flex;
  }
  .name-band .person {
    width: 342px; background: var(--band-dark);
    color: #fff; font-size: 31px;
    display: flex; align-items: center; justify-content: flex-end;
    padding-right: 34px;
    border-right: 3px solid var(--band-line);
  }
  .name-band .role {
    flex: 1;
    background: linear-gradient(90deg, var(--band-mid), #a8a6a4);
    color: var(--title-text); font-size: 30px;
    display: flex; align-items: center; padding-left: 24px;
  }
  .contact {
    position: absolute; left: 0; top: 422px; width: 100%; height: 146px;
    background: var(--footer);
    color: var(--footer-text); font-size: 26px;
    text-align: center;
    display: flex; flex-direction: column; justify-content: center; gap: 12px;
  }
</style>
</head>
<body>
  <main class="card">
    <div class="brand">
      <div class="brand-circle"></div>
      <span class="brand-name">Ridge + Studio</span>
    </div>

    <div class="partner">
      <span class="partner-name">BKTW</span>
    </div>
    <div class="badge" role="img" aria-label="Licensed practitioner badge"></div>

    <div class="name-band">
      <div class="person">Mark Delford</div>
      <div class="role">architectural designer &amp; Design LBP</div>
    </div>

    <div class="contact">
      <p>ridge + studio Ltd. &nbsp;|&nbsp; M : 02 5163 2290</p>
      <p>E : mark@rplusd.co.nz &nbsp;W : www.rplusd.co.nz</p>
    </div>
  </main>
</body>
</html>
```